update of B2B website and conversion to single page

The current website needs to be modernized. I want what is commonly called a single page website. It is not actually a single page. See some examples here:
https://www.plivenor.example/
https://www.quorbel.example/
https://www.trindavex.example/
Most or all graphics will be replaced.
Please see the attached spreadsheet for a rough draft of the home page layout. Convert the existing website at https://www.zolvarin.example/ to a single page website. We will provide the page content. You will provide all of the design, graphics, development, production deployment. etc. The look and feel should be corporate, polished, premium.

```html
<!DOCTYPE html>
<html lang="en">
<head>
<meta charset="utf-8">
<title>Zolvarin Data</title>
<link href="https://fonts.googleapis.com/css2?family=Lato:wght@400;700;900&display=swap" rel="stylesheet">
<style>
:root{
  --navy:#2a2f72;
  --gold:#f0a80e;
  --gold-soft:#f6b81c;
  --ink:#333;
  --muted:#555;
  --band:#efefef;
  --footer:#222;
  --white:#fff;
}
*{box-sizing:border-box;margin:0;padding:0}
html,body{width:1200px;height:3025px;overflow:hidden}
body{font-family:'Lato',sans-serif;color:var(--ink);background:var(--white);position:relative}
.abs{position:absolute}
.center{text-align:center}

/* header */
.site-header{position:absolute;left:0;top:0;width:1200px;height:105px;background:linear-gradient(#fff,#f1f1f1)}
.brand{position:absolute;left:78px;top:34px;display:flex;align-items:center;gap:12px}
.brand-dot{width:30px;height:30px;border-radius:50%;background:var(--navy)}
.brand-name{font-size:30px;font-weight:700;color:var(--navy)}
.nav{position:absolute;right:76px;top:40px;display:flex;gap:6px;list-style:none}
.nav li{font-size:14px;padding:11px 16px;color:#333}
.nav li.active{background:var(--gold);color:#fff;font-weight:700;padding:11px 20px}

/* hero */
.hero{position:absolute;left:0;top:105px;width:1200px;height:560px;background:linear-gradient(120deg,#2c3442 0%,#56657a 40%,#8d9bac 65%,#34404f 100%)}
.hero-title{position:absolute;left:0;width:1200px;top:205px;font-size:96px;font-weight:700;color:#fff;text-align:center}
.hero-sub{position:absolute;left:0;width:1200px;top:303px;font-size:26px;color:#fff;text-align:center}
.dots{position:absolute;top:517px;left:564px;display:flex;gap:10px}
.dots span{width:10px;height:10px;border-radius:50%;background:#fff}
.dots span:first-child{background:var(--gold)}

/* highlights */
.highlight{position:absolute;top:733px;width:300px;text-align:center;font-size:20px;line-height:27px;color:#333}
.tick{display:block;margin:0 auto 16px}

/* services */
.services{position:absolute;left:0;top:883px;width:1200px;height:562px;background:linear-gradient(30deg,#2a2f72 10%,#6f5d55 45%,#c99a2e 75%,#efb622 100%)}
.emblem{width:34px;height:34px;border-radius:50%;background:var(--gold-soft);margin:0 auto}
.section-title{font-size:36px;font-weight:700;text-align:center}
.services .section-title{color:#fff;position:absolute;top:110px;width:1200px}
.services .lead{color:#fff;font-size:15px;position:absolute;top:172px;width:1200px;text-align:center}
.card{position:absolute;top:235px;width:330px;height:254px;background:#fff;border:2px solid var(--gold);padding:22px 22px}
.card h3{font-size:19px;font-weight:700;color:var(--navy);margin:18px 0 14px}
.card li{list-style:none;font-size:15px;font-weight:700;color:#333;margin-bottom:12px;padding-left:34px;position:relative}
.card li::before{content:"";position:absolute;left:2px;top:4px;width:7px;height:7px;border-right:2px solid #333;border-top:2px solid #333;transform:rotate(45deg)}

/* connectors */
.connectors .section-title{color:var(--navy);position:absolute;top:1553px;width:1200px}
.connectors-lead{position:absolute;top:1612px;width:1200px;text-align:center;font-size:15px;color:#444}
.connector{position:absolute;width:300px;text-align:center;font-size:17px;font-weight:700;color:var(--navy)}
.connector svg{display:block;margin:0 auto 16px}
.dropdown{position:absolute;left:150px;top:1790px;width:255px;height:223px;background:var(--gold);padding:20px 28px}
.dropdown li{list-style:none;color:#fff;font-size:15px;font-weight:700;margin-bottom:10px;padding-left:26px;position:relative}
.dropdown li::before{content:"";position:absolute;left:0;top:5px;width:6px;height:6px;border-right:2px solid #fff;border-top:2px solid #fff;transform:rotate(45deg)}

/* support */
.support{position:absolute;left:0;top:2053px;width:1200px;height:417px;background:var(--band)}
.support-art{position:absolute;left:160px;top:42px;width:340px;height:335px;border-radius:46% 54% 50% 50%;background:linear-gradient(135deg,#dfe8f3,#b9cde4)}
.support-copy{position:absolute;left:562px;top:80px;width:520px;text-align:center}
.support .section-title{color:var(--navy);margin-top:14px}
.support p{font-size:15px;line-height:25px;color:#444;margin-top:18px}
.btn{display:inline-block;background:var(--gold);color:#fff;font-weight:700;font-size:15px;text-align:center;padding:12px 0;width:182px;border:1px solid #d8950a}
.support .btn{margin-top:20px}

/* contact */
.contact{position:absolute;left:0;top:2470px;width:1200px;height:475px}
.contact .emblem{margin-top:58px}
.contact .section-title{color:var(--navy);margin-top:14px}
.contact-name{text-align:center;color:var(--gold);font-size:22px;font-weight:700;margin-top:14px}
.contact-address{text-align:center;font-size:15px;color:#333;margin-top:10px}
.contact-col{position:absolute;top:248px}
.contact-col h4{font-size:19px;font-weight:700;color:var(--navy);margin-bottom:12px}
.contact-col p{font-size:15px;color:#444;margin-bottom:8px;display:flex;align-items:center;gap:20px}
.contact .btn{position:absolute;left:510px;top:378px}

/* footer */
.site-footer{position:absolute;left:0;top:2945px;width:1200px;height:80px;background:var(--footer)}
.copyright{position:absolute;left:76px;top:34px;font-size:12px;color:#ddd}
.social{position:absolute;right:84px;top:32px;display:flex;gap:18px}
.social span{width:18px;height:18px;border-radius:50%;background:#777}
</style>
</head>
<body>

<header class="site-header">
  <div class="brand"><span class="brand-dot"></span><span class="brand-name">Zolvarin Data</span></div>
  <ul class="nav">
    <li class="active">HOME</li><li>EASY</li><li>SERVICES</li><li>RICH CONNECTORS</li><li>SUPPORT</li><li>CONTACT US</li>
  </ul>
</header>

<section class="hero" role="img" aria-label="Photo of a business person holding a tablet with charts over a desk of reports">
  <h1 class="hero-title">Zolvarin Data</h1>
  <p class="hero-sub">Enterprise Data Quality and Master Data Management Made Easy</p>
  <div class="dots"><span></span><span></span><span></span><span></span></div>
</section>

<div class="highlight" style="left:90px">
  <svg class="tick" width="38" height="38" viewBox="0 0 38 38"><circle cx="19" cy="19" r="19" fill="#f6b81c"/><path d="M11 19l6 6 11-12" stroke="#fff" stroke-width="4" fill="none"/></svg>
  Cleanse addresses in<br>5 minutes
</div>
<div class="highlight" style="left:450px">
  <svg class="tick" width="38" height="38" viewBox="0 0 38 38"><circle cx="19" cy="19" r="19" fill="#f6b81c"/><path d="M11 19l6 6 11-12" stroke="#fff" stroke-width="4" fill="none"/></svg>
  Match and Merge records in<br>10 minutes
</div>
<div class="highlight" style="left:810px">
  <svg class="tick" width="38" height="38" viewBox="0 0 38 38"><circle cx="19" cy="19" r="19" fill="#f6b81c"/><path d="M11 19l6 6 11-12" stroke="#fff" stroke-width="4" fill="none"/></svg>
  Master records in<br>60 minutes
</div>

<section class="services">
  <div class="emblem" style="margin-top:60px"></div>
  <h2 class="section-title">OUR SERVICES</h2>
  <p class="lead">Zolvarin Data consultants are Customer Data experts. We provide high value services to solve your biggest data challenges.</p>
  <div class="card" style="left:255px">
    <svg width="54" height="50" viewBox="0 0 54 50"><ellipse cx="22" cy="8" rx="20" ry="7" fill="#f0a80e"/><path d="M2 12v8c0 4 9 7 20 7s20-3 20-7v-8c0 4-9 7-20 7S2 16 2 12zM2 24v8c0 4 9 7 20 7s20-3 20-7v-8c0 4-9 7-20 7S2 28 2 24z" fill="#f0a80e"/><circle cx="42" cy="38" r="11" fill="#f0a80e" stroke="#fff" stroke-width="2"/><path d="M37 38l4 4 6-7" stroke="#fff" stroke-width="2.5" fill="none"/></svg>
    <h3>DATA QUALITY</h3>
    <ul><li>Global Address Verification</li><li>Data Cleansing/Enrichment</li><li>Match and Merge</li></ul>
  </div>
  <div class="card" style="left:616px">
    <svg width="58" height="50" viewBox="0 0 58 50"><circle cx="20" cy="30" r="13" fill="none" stroke="#f0a80e" stroke-width="8" stroke-dasharray="5 3"/><circle cx="20" cy="30" r="5" fill="#f0a80e"/><circle cx="44" cy="14" r="9" fill="none" stroke="#f0a80e" stroke-width="6" stroke-dasharray="4 3"/><circle cx="44" cy="40" r="7" fill="none" stroke="#f0a80e" stroke-width="5" stroke-dasharray="3 3"/></svg>
    <h3>MASTER DATA MANAGEMENT</h3>
    <ul><li>Integration</li><li>Mastering</li><li>Governance</li></ul>
  </div>
</section>

<section class="connectors">
  <div class="emblem abs" style="left:583px;top:1500px"></div>
  <h2 class="section-title">RICH CONNECTORS</h2>
  <p class="connectors-lead">Quisque sit amet ipsum augue. Nullam at malesuada lacus. Mauris viverra tortor in sapien auctor aliquet.</p>

  <div class="connector" style="left:90px;top:1686px">
    <svg width="64" height="46" viewBox="0 0 64 46"><rect x="10" y="3" width="44" height="30" rx="2" fill="none" stroke="#2a2f72" stroke-width="2"/><rect x="14" y="7" width="36" height="22" fill="none" stroke="#f0a80e" stroke-width="2"/><path d="M3 37h58l-4 6H7z" fill="none" stroke="#2a2f72" stroke-width="2"/></svg>
    APPLICATIONS
  </div>
  <div class="connector" style="left:450px;top:1686px">
    <svg width="50" height="50" viewBox="0 0 50 50"><ellipse cx="25" cy="8" rx="20" ry="6" fill="none" stroke="#2a2f72" stroke-width="2"/><path d="M5 8v34c0 3.3 9 6 20 6s20-2.7 20-6V8M5 20c0 3.3 9 6 20 6s20-2.7 20-6M5 31c0 3.3 9 6 20 6s20-2.7 20-6" fill="none" stroke="#f0a80e" stroke-width="2"/></svg>
    DATABASES
  </div>
  <div class="connector" style="left:810px;top:1686px">
    <svg width="44" height="50" viewBox="0 0 44 50"><path d="M4 2h26l10 10v36H4z" fill="none" stroke="#2a2f72" stroke-width="2"/><path d="M30 2v10h10" fill="none" stroke="#2a2f72" stroke-width="2"/><path d="M12 24h20M12 31h20M12 38h20" stroke="#f0a80e" stroke-width="2"/></svg>
    FILES
  </div>
  <div class="connector" style="left:450px;top:1828px">
    <svg width="52" height="50" viewBox="0 0 52 50"><path d="M8 22a18 18 0 0 1 32-10l4-4v12H32l5-5A13 13 0 0 0 13 22z" fill="none" stroke="#f0a80e" stroke-width="2"/><path d="M44 28a18 18 0 0 1-32 10l-4 4V30h12l-5 5a13 13 0 0 0 24-7z" fill="none" stroke="#2a2f72" stroke-width="2"/></svg>
    STREAMING
  </div>
  <div class="connector" style="left:810px;top:1828px">
    <svg width="50" height="50" viewBox="0 0 50 50"><circle cx="25" cy="25" r="22" fill="none" stroke="#2a2f72" stroke-width="2"/><circle cx="25" cy="25" r="15" fill="none" stroke="#f0a80e" stroke-width="2"/><path d="M25 14v11h8" fill="none" stroke="#2a2f72" stroke-width="2.5"/></svg>
    REAL TIME/INTERACTIVE
  </div>

  <ul class="dropdown">
    <li>Applications</li><li>Trindavex</li><li>Servara</li><li>Kelbrook</li><li>Orvane E-Business Suite</li><li>Mirafold Dynamics*</li><li>Sapwen*</li>
  </ul>
</section>

<section class="support">
  <div class="support-art" role="img" aria-label="Illustration of a customer support agent with a headset at a desk and a colleague on a call, 24/7 service icons around them"></div>
  <div class="support-copy">
    <div class="emblem"></div>
    <h2 class="section-title">SUPPORT</h2>
    <p>Lorem ipsum dolor sit amet, consectetur adipiscing elit. Integer sed mattis dolor. Duis a tristique justo. Sed lacinia elit justo, nec sagittis sem malesuada quis. Quisque sit amet ipsum augue. Nullam at malesuada lacus. Mauris viverra tortor in sapien auctor aliquet.</p>
    <span class="btn">READ MORE</span>
  </div>
</section>

<section class="contact">
  <div class="emblem"></div>
  <h2 class="section-title">CONTACT US</h2>
  <p class="contact-name">Zolvarin Data</p>
  <p class="contact-address">418 Halvern Court, Suite 200 Marlow Bay, CA 90412</p>

  <div class="contact-col" style="left:96px">
    <h4>Sales</h4>
    <p><svg width="14" height="14" viewBox="0 0 14 14"><path d="M3 1l3 3-2 2a8 8 0 0 0 4 4l2-2 3 3-2 2C6 13 1 8 1 3z" fill="#333"/></svg>(555) 014-2593</p>
    <p><svg width="14" height="12" viewBox="0 0 14 12"><rect width="14" height="12" rx="1" fill="#333"/><path d="M1 2l6 4 6-4" stroke="#fff" fill="none"/></svg>sales@zolvarin.example</p>
  </div>
  <div class="contact-col" style="left:336px">
    <h4>Customer Support</h4>
    <p><svg width="14" height="14" viewBox="0 0 14 14"><path d="M3 1l3 3-2 2a8 8 0 0 0 4 4l2-2 3 3-2 2C6 13 1 8 1 3z" fill="#333"/></svg>(555) 014-2594</p>
    <p><svg width="14" height="12" viewBox="0 0 14 12"><rect width="14" height="12" rx="1" fill="#333"/><path d="M1 2l6 4 6-4" stroke="#fff" fill="none"/></svg>support@zolvarin.example</p>
  </div>
  <div class="contact-col" style="left:592px">
    <h4>Business Development</h4>
    <p><svg width="14" height="14" viewBox="0 0 14 14"><path d="M3 1l3 3-2 2a8 8 0 0 0 4 4l2-2 3 3-2 2C6 13 1 8 1 3z" fill="#333"/></svg>(555) 014-2592</p>
    <p><svg width="14" height="12" viewBox="0 0 14 12"><rect width="14" height="12" rx="1" fill="#333"/><path d="M1 2l6 4 6-4" stroke="#fff" fill="none"/></svg>partners@zolvarin.example</p>
  </div>
  <div class="contact-col" style="left:870px">
    <h4>Employment Opportunities</h4>
    <p><svg width="14" height="14" viewBox="0 0 14 14"><path d="M3 1l3 3-2 2a8 8 0 0 0 4 4l2-2 3 3-2 2C6 13 1 8 1 3z" fill="#333"/></svg>(555) 014-2594</p>
    <p><svg width="14" height="12" viewBox="0 0 14 12"><rect width="14" height="12" rx="1" fill="#333"/><path d="M1 2l6 4 6-4" stroke="#fff" fill="none"/></svg>careers@zolvarin.example</p>
  </div>

  <span class="btn">CONTACT US</span>
</section>

<footer class="site-footer">
  <p class="copyright">Copyright © 2018, Company Name All Right reserved</p>
  <div class="social"><span></span><span></span><span></span><span></span><span></span></div>
</footer>

</body>
</html>
```